Luxury Wine Label for New Startup Winery

We need a wine label for our new winery startup. We have worked with a local designer but do not feel the resulting label / logo have the elevation required to present our brand as a luxury wine. Our winery is called "Quailbrook Vineyards" and we are focused on extremely high quality hand crafted artisan and estate wines from the Pacific Northwest.
We would like to see designs that utilize a tree line, or other imagery that represents the "Quailbrook" part of our company name. Another interesting feature could be wood grain.
A logo will be required based on your design so please design with this in mind:
This logo should be consistent with the wine bottle label design, and should be representative of our high end exclusive wine while giving a sense of place (Oregon/ Pacific Northwest.)
I will supply an image of the design we received from our local designer, PLEASE NOTE: in general we do like wood grain and tree line concepts but feel the execution was poorly done.
ATTN: Logo design should be suitable for use on: Bottles (Red wine/rose/white wine), Bussiness cards, vehicle signage, business signage, etc
P.S.:
If you have a design that is not outside the box we are still interested in seeing it.
Label is for a burgundy style bottle with a label height of 3.5 - 4" and a width of 3.5-4"
any label <= 4"x4" and >=3.5"x3.5" will be acceptable:
HOWEVER Width should be greater than or equal to height due to the bottle format
Target Market(s)
Wine enthusiasts with adequate discretionary budgets to afford $100 bottles of wine.
Industry/Entity Type
Wine / Winery
Requirements
Must have
- A sense of luxury, a feel of exclusivity, and a theme consistent with our product and brand name
Nice to have
- Tree line, wood grain or other wood themes. Serif fonts
Should not have
- anything cheesy, off topic, hard to read script fonts or anything that makes the label hard to read from a few feet away or too busy

```html
<!DOCTYPE html>
<html lang="en">
<head>
<meta charset="utf-8">
<title>Quailbrook Vineyards — Syrah Label</title>
<link rel="stylesheet" href="https://fonts.googleapis.com/css2?family=Cinzel:wght@400;600&family=Raleway:wght@400&display=swap">
<style>
  :root {
    --page: #ffffff;
    --panel: #3a3a3b;
    --rule: #8c8c8e;
    --gold: #b8893a;
    --ink-light: #f2f0ec;
    --wood-dark: #3b2a20;
    --wood-mid: #5e4636;
    --wood-light: #7a5d48;
    --varietal: #e9dcc6;
  }
  * { margin: 0; padding: 0; box-sizing: border-box; }
  html, body {
    width: 840px;
    height: 1200px;
    overflow: hidden;
    background: var(--page);
  }
  .canvas {
    position: relative;
    width: 840px;
    height: 1200px;
  }
  .label {
    position: absolute;
    left: 60px;
    top: 214px;
    width: 720px;
  }
  .label__panel {
    position: relative;
    height: 580px;
    background: var(--panel);
    text-align: center;
  }
  .label__rule {
    position: absolute;
    left: 26px;
    right: 26px;
    height: 3px;
    background: var(--rule);
  }
  .label__rule--top { top: 26px; }
  .label__rule--bottom { bottom: 20px; }
  .brand {
    position: absolute;
    left: 0;
    right: 0;
    top: 120px;
    display: flex;
    flex-direction: column;
    align-items: center;
  }
  .brand__mark {
    width: 28px;
    height: 28px;
    background: var(--gold);
    margin-bottom: 70px;
  }
  .brand__name,
  .brand__sub {
    font-family: "Cinzel", serif;
    font-weight: 400;
    color: var(--ink-light);
    text-transform: uppercase;
    line-height: 1;
  }
  .brand__name {
    font-size: 64px;
    letter-spacing: 0.04em;
  }
  .brand__sub {
    margin-top: 18px;
    font-size: 34px;
    letter-spacing: 0.12em;
  }
  .label__region {
    position: absolute;
    left: 0;
    right: 0;
    top: 470px;
    font-family: "Raleway", sans-serif;
    font-size: 32px;
    color: var(--ink-light);
    letter-spacing: 0.01em;
    text-transform: uppercase;
  }
  .label__band {
    position: relative;
    margin-top: 38px;
    height: 154px;
    display: flex;
    align-items: center;
    justify-content: center;
  }
  .label__wood {
    position: absolute;
    inset: 0;
    background: linear-gradient(180deg, var(--wood-dark) 0%, var(--wood-mid) 35%, var(--wood-light) 55%, var(--wood-mid) 75%, var(--wood-dark) 100%);
  }
  .label__varietal {
    position: relative;
    font-family: "Cinzel", serif;
    font-weight: 600;
    font-size: 50px;
    letter-spacing: 0.12em;
    color: var(--varietal);
  }
</style>
</head>
<body>
<main class="canvas">
  <section class="label">
    <div class="label__panel">
      <span class="label__rule label__rule--top"></span>
      <div class="brand">
        <span class="brand__mark"></span>
        <span class="brand__name">Quailbrook</span>
        <span class="brand__sub">Vineyards</span>
      </div>
      <p class="label__region">Willamette Valley</p>
      <span class="label__rule label__rule--bottom"></span>
    </div>
    <div class="label__band">
      <div class="label__wood" role="img" aria-label="Dark brown wood grain texture band"></div>
      <span class="label__varietal">SYRAH</span>
    </div>
  </section>
</main>
</body>
</html>
```